Looking for a modern, Professional business card design

We have a simple business card, but are looking for a more modern, professional look. A sample of the basic card is attached as well as the logo. We would also like to add that we offer:
Struggling with your finances?
- Learn to become debt free
- Discover the power of cash
- Control your money instead of it controlling you
Let us help you achieve a new level of financial freedom!
Also, we would like to have a "SPECIAL OFFER!: FREE 30 minute consultation"
Financial Planning

```html
<!DOCTYPE html>
<html lang="en">
<head>
<meta charset="utf-8">
<title>Clearpath Money Coaching – Business Cards</title>
<link href="https://fonts.googleapis.com/css2?family=Josefin+Sans:wght@400;600;700&family=Russo+One&display=swap" rel="stylesheet">
<style>
  :root {
    --bg: #2b2b2d;
    --card: #ffffff;
    --green-dark: #2f8a36;
    --green-mid: #4ea83a;
    --green-light: #8cc63f;
    --ink: #1a1a1a;
    --white: #ffffff;
  }
  * { box-sizing: border-box; margin: 0; padding: 0; }
  html, body { width: 1200px; height: 900px; overflow: hidden; }
  body { background: var(--bg); font-family: "Josefin Sans", sans-serif; color: var(--ink); position: relative; }

  .card {
    position: absolute; width: 700px; height: 400px; background: var(--card);
    overflow: hidden; box-shadow: 0 10px 30px rgba(0,0,0,.45);
  }
  .card--front { left: 60px; top: 40px; }
  .card--back { left: 440px; top: 460px; }

  /* Front */
  .brand-mark {
    position: absolute; left: 60px; top: 168px;
    display: flex; align-items: center; gap: 12px;
    font-weight: 700; font-size: 26px; color: var(--green-mid); letter-spacing: .5px;
  }
  .brand-mark .dot { width: 22px; height: 22px; border-radius: 50%; background: var(--green-light); }

  .pitch { position: absolute; right: 50px; top: 110px; text-align: right; font-size: 18px; line-height: 1.6; }
  .pitch__headline {
    display: inline-block; border: 2.5px solid var(--ink); border-radius: 18px;
    padding: 5px 14px 2px; font-size: 19px; font-weight: 600; margin-bottom: 10px;
  }
  .accent { color: var(--green-light); font-weight: 700; }
  .pitch__list { list-style: none; margin-bottom: 4px; }
  .pitch__list li::after {
    content: ""; display: inline-block; width: 8px; height: 8px; border-radius: 50%;
    background: var(--green-light); margin-left: 10px; vertical-align: 3px;
  }
  .pitch__close { margin-right: 18px; }

  /* Back */
  .panel { position: absolute; inset: 0; }
  .holder { position: absolute; left: 0; top: 76px; }
  .holder__bar { position: absolute; left: 0; top: 4px; width: 44px; height: 40px; background: var(--ink); }
  .holder__name { margin-left: 56px; font-family: "Russo One", sans-serif; font-size: 24px; color: var(--green-light); letter-spacing: 1px; }
  .holder__role { margin-left: 56px; font-family: "Russo One", sans-serif; font-size: 13px; color: var(--ink); letter-spacing: 1px; }

  .contact { position: absolute; right: 36px; top: 44px; text-align: right; color: var(--white); }
  .contact__brand {
    display: flex; justify-content: flex-end; align-items: center; gap: 9px;
    font-weight: 700; font-size: 22px; margin-bottom: 30px;
  }
  .contact__brand .dot { width: 14px; height: 14px; border-radius: 50%; background: var(--white); }
  .contact__line { display: flex; justify-content: flex-end; align-items: center; gap: 10px; font-size: 19px; line-height: 1.6; }
  .contact__line svg { width: 15px; height: 15px; flex: none; }
  .offer { position: absolute; right: 36px; bottom: 46px; font-size: 19px; color: var(--ink); }
  .offer__label { font-family: "Russo One", sans-serif; font-size: 15px; }
  .offer__free { font-family: "Russo One", sans-serif; font-size: 15px; color: var(--white); margin-left: 5px; }
</style>
</head>
<body>

<section class="card card--front">
  <div class="brand-mark"><span class="dot"></span>Clearpath</div>
  <div class="pitch">
    <div class="pitch__headline"><span class="accent">STRUGGLING</span> WITH YOUR <span class="accent">FINANCES?</span></div>
    <ul class="pitch__list">
      <li>Learn to become debt free</li>
      <li>Discover the power of cash</li>
      <li>Control your money instead of it controlling you</li>
    </ul>
    <p class="pitch__close">Let us help you achieve a new level of financial <span class="accent">FREEDOM!</span></p>
  </div>
</section>

<section class="card card--back">
  <svg class="panel" viewBox="0 0 700 400" aria-hidden="true">
    <defs>
      <linearGradient id="panelFill" x1="0" y1="0" x2="1" y2="1">
        <stop offset="0" stop-color="#3f9a3e"/>
        <stop offset="1" stop-color="#2f8a36"/>
      </linearGradient>
    </defs>
    <path d="M345 0 H700 V400 H270 C310 290 338 150 345 0 Z" fill="url(#panelFill)"/>
  </svg>

  <div class="holder">
    <span class="holder__bar"></span>
    <p class="holder__name">DANIEL R. HAYES</p>
    <p class="holder__role">PERSONAL FINANCIAL COACH</p>
  </div>

  <div class="contact">
    <div class="contact__brand"><span class="dot"></span>Clearpath Money Coaching</div>
    <p class="contact__line">(555) 014-2738
      <svg viewBox="0 0 16 16"><rect x="4" y="1" width="8" height="14" rx="1.5" fill="none" stroke="#8cc63f" stroke-width="1.5"/></svg></p>
    <p class="contact__line">daniel@clearpathmoney.com
      <svg viewBox="0 0 16 16"><rect x="1" y="3" width="14" height="10" fill="none" stroke="#8cc63f" stroke-width="1.5"/><path d="M1 3 L8 9 L15 3" fill="none" stroke="#8cc63f" stroke-width="1.5"/></svg></p>
    <p class="contact__line">www.clearpathmoney.com
      <svg viewBox="0 0 16 16"><circle cx="8" cy="8" r="6.5" fill="none" stroke="#8cc63f" stroke-width="1.5"/><path d="M1.5 8 H14.5 M8 1.5 C4 5 4 11 8 14.5 C12 11 12 5 8 1.5" fill="none" stroke="#8cc63f" stroke-width="1.2"/></svg></p>
  </div>

  <p class="offer"><span class="offer__label">SPECIAL OFFER!</span><span class="offer__free">FREE</span> 30 minute consultation</p>
</section>

</body>
</html>
```